IT Company requires new Business Card design.

Over the years we have had a few different business card designs. We are now due for new cards across the board for all staff. We felt this would be a good time to start fresh with a new design. Our traditional card simply had our details on the front, and a list of services on the back. We don't particularly need the list of services, we have had cards where the only thing on the rear of the card was our logo.
Feel free to be creative, we would like our tag line "Complete IT Management" to appear at some point, doesn't necessarily have to be with the logo.
I have attached samples and drafts of various previous cards we have used over the years.

```html
<!DOCTYPE html>
<html lang="en">
<head>
<meta charset="utf-8">
<title>Ridgeline Networking – Business Card</title>
<link href="https://fonts.googleapis.com/css2?family=Open+Sans:wght@400;600;700;800&display=swap" rel="stylesheet">
<style>
  :root {
    --backdrop: #e7e8ec;
    --slate: #5f7381;
    --swoosh: #4b4e52;
    --paper: #ffffff;
    --ink: #454a4f;
  }
  * { box-sizing: border-box; margin: 0; padding: 0; }
  html, body {
    width: 1200px; height: 987px; overflow: hidden;
    background: var(--backdrop);
    font-family: "Open Sans", Arial, sans-serif;
  }
  .canvas { position: relative; width: 1200px; height: 987px; }

  .card {
    position: absolute;
    width: 560px; height: 320px;
    border-radius: 26px;
    overflow: hidden;
    box-shadow: 0 10px 28px rgba(40, 50, 60, 0.18);
  }

  /* Back of card */
  .card-back { left: 590px; top: 110px; background: var(--slate); color: var(--paper); }
  .card-back .brand {
    position: absolute; left: 0; right: 0; top: 100px;
    display: flex; align-items: center; justify-content: center; gap: 16px;
  }
  .card-back .brand-square { width: 46px; height: 46px; background: var(--paper); }
  .card-back .brand-name {
    font-weight: 800; font-size: 34px; line-height: 1; letter-spacing: 1px; text-transform: uppercase;
  }
  .card-back .tagline {
    position: absolute; left: 0; right: 0; top: 186px; text-align: center;
    font-size: 14px; font-weight: 400; letter-spacing: 5px; text-transform: uppercase;
  }

  /* Front of card */
  .card-front { left: 50px; top: 560px; background: var(--paper); }
  .card-front .wave { position: absolute; inset: 0; }
  .card-front .brand {
    position: absolute; left: 170px; top: 34px;
    display: flex; align-items: center; gap: 14px;
  }
  .card-front .brand-square { width: 56px; height: 56px; background: var(--slate); }
  .card-front .brand-name {
    color: var(--slate); font-weight: 800; font-size: 32px; line-height: 0.95; text-transform: uppercase;
  }
  .card-front .address {
    position: absolute; left: 172px; top: 112px;
    font-size: 13px; color: var(--ink);
  }
  .card-front .person { position: absolute; left: 22px; top: 196px; color: var(--paper); }
  .card-front .person-name { font-weight: 700; font-size: 16px; line-height: 1.3; }
  .card-front .person-role { font-size: 12.5px; }
  .card-front .contacts {
    position: absolute; right: 26px; bottom: 16px;
    display: flex; align-items: flex-end; gap: 26px; color: var(--paper); font-size: 12.5px;
  }
  .contact-list { list-style: none; display: flex; flex-direction: column; gap: 3px; }
  .contact-item { display: flex; align-items: center; gap: 8px; line-height: 1.35; }
  .contact-item svg { width: 13px; height: 13px; flex: none; }
</style>
</head>
<body>
<main class="canvas">

  <section class="card card-back" aria-label="Back of business card">
    <div class="brand">
      <span class="brand-square"></span>
      <span class="brand-name">Ridgeline Networking</span>
    </div>
    <p class="tagline">Complete IT Management</p>
  </section>

  <section class="card card-front" aria-label="Front of business card">
    <svg class="wave" viewBox="0 0 560 320" aria-hidden="true">
      <path d="M0 0 L60 0 C80 120 150 200 260 215 C380 232 470 228 560 236 L560 320 L0 320 Z" fill="var(--slate)"/>
      <path transform="translate(8 -8)" d="M60 0 C80 120 150 200 260 215 C380 232 470 228 560 236" fill="none" stroke="var(--swoosh)" stroke-width="4"/>
      <path transform="translate(18 -18)" d="M60 0 C80 120 150 200 260 215 C380 232 470 228 560 236" fill="none" stroke="var(--slate)" stroke-width="1.2"/>
    </svg>

    <div class="brand">
      <span class="brand-square"></span>
      <span class="brand-name">Ridgeline<br>Networking</span>
    </div>
    <p class="address">Unit 4 18 Marlow Street, Bayview WA 6100</p>

    <div class="person">
      <p class="person-name">Daniel Carter</p>
      <p class="person-role">Operation Manager</p>
    </div>

    <div class="contacts">
      <p class="contact-item">
        <svg viewBox="0 0 16 16" aria-hidden="true"><rect x="1" y="3" width="14" height="10" rx="1.5" fill="none" stroke="currentColor" stroke-width="1.6"/><path d="M1.5 4 L8 9 L14.5 4" fill="none" stroke="currentColor" stroke-width="1.6"/></svg>
        daniel@ridgelinenetworking.com.au
      </p>
      <ul class="contact-list">
        <li class="contact-item">
          <svg viewBox="0 0 16 16" aria-hidden="true"><path d="M4 1.5 L6.5 4.5 L5 6.5 C6 8.5 7.5 10 9.5 11 L11.5 9.5 L14.5 12 L12.5 14.5 C7 14 2 9 1.5 3.5 Z" fill="currentColor"/></svg>
          08 9350 1184
        </li>
        <li class="contact-item">
          <svg viewBox="0 0 16 16" aria-hidden="true"><rect x="4" y="1" width="8" height="14" rx="1.5" fill="currentColor"/><rect x="5.5" y="3" width="5" height="6" fill="var(--slate)"/></svg>
          0412 608 975
        </li>
        <li class="contact-item">
          <svg viewBox="0 0 16 16" aria-hidden="true"><rect x="4" y="1" width="8" height="5" fill="currentColor"/><rect x="1" y="6" width="14" height="7" rx="1" fill="currentColor"/><rect x="4" y="10" width="8" height="5" fill="var(--paper)" stroke="var(--slate)"/></svg>
          08 9350 1184
        </li>
      </ul>
    </div>
  </section>

</main>
</body>
</html>
```